Professional & attention grabbing.

A business card design, front and back. I already have a logo I will attach, but I am open to something new as well.
Things to include:
Name:
Title:
Phone:
Email:
Wanting something that is professional but attention grabbing.
Also we do a lot of work using drones on natural gas pipelines (leading the future)if you want to include any of that. I'm open to ideas.
Target Market(s)
Natural gas transmission industry / greenhouse gas mitigation industry
Industry/Entity Type
Business
Colors
Designer to choose colors to be used in the design.
Look and feel
Each slider illustrates characteristics of the customer's brand and the style your logo design should communicate.

```html
<!DOCTYPE html>
<html lang="en">
<head>
<meta charset="utf-8">
<title>Orvane Inspections – Business Card</title>
<link href="https://fonts.googleapis.com/css2?family=Montserrat:wght@500;600;700&display=swap" rel="stylesheet">
<style>
  :root {
    --stage: #1d1d1f;
    --card-dark: #3b3b3e;
    --ink-dark: #2b2b2e;
    --accent-red: #c8202a;
    --paper: #ffffff;
    --text-light: #f2f2f2;
  }
  * { box-sizing: border-box; margin: 0; padding: 0; }
  html, body {
    width: 1200px;
    height: 1000px;
    overflow: hidden;
    background: var(--stage);
    font-family: "Montserrat", Arial, sans-serif;
  }
  .card {
    position: absolute;
    width: 525px;
    height: 300px;
    border-radius: 22px;
    overflow: hidden;
    background: var(--card-dark);
    box-shadow: 0 18px 40px rgba(0,0,0,0.45);
  }
  .card--back { left: 110px; top: 130px; }
  .card--front { left: 565px; top: 560px; }

  .wordmark {
    display: flex;
    align-items: center;
    gap: 14px;
    font-weight: 700;
    letter-spacing: 0.5px;
  }
  .wordmark__square { width: 34px; height: 34px; flex: none; }

  .card--back .wordmark {
    position: absolute;
    left: 0; right: 0; top: 50%;
    transform: translateY(-50%);
    justify-content: center;
    color: var(--text-light);
    font-size: 30px;
  }
  .card--back .wordmark__square { background: var(--text-light); }

  .card__shapes { position: absolute; inset: 0; }

  .card--front .wordmark {
    position: absolute;
    left: 300px;
    top: 92px;
    color: var(--ink-dark);
    font-size: 22px;
    line-height: 1.1;
  }
  .card--front .wordmark__square { background: var(--accent-red); width: 30px; height: 30px; }

  .contact {
    position: absolute;
    left: 36px;
    top: 170px;
    color: var(--text-light);
  }
  .contact__name {
    color: var(--accent-red);
    font-weight: 700;
    font-size: 18px;
    letter-spacing: 0.5px;
    text-transform: uppercase;
  }
  .contact__title {
    font-weight: 500;
    font-size: 12px;
    letter-spacing: 0.5px;
    margin-top: 2px;
  }
  .contact__list { list-style: none; margin-top: 14px; }
  .contact__item {
    display: flex;
    align-items: center;
    gap: 10px;
    font-size: 13px;
    font-weight: 500;
    margin-bottom: 4px;
  }
  .contact__icon { width: 12px; height: 12px; fill: var(--accent-red); }
</style>
</head>
<body>

  <section class="card card--back" aria-label="Card back">
    <div class="wordmark">
      <span class="wordmark__square"></span>
      <span class="wordmark__name">Orvane Inspections</span>
    </div>
  </section>

  <section class="card card--front" aria-label="Card front">
    <svg class="card__shapes" viewBox="0 0 525 300" width="525" height="300" aria-hidden="true">
      <circle cx="485" cy="60" r="292" fill="var(--accent-red)"/>
      <circle cx="490" cy="60" r="284" fill="var(--paper)"/>
      <circle cx="500" cy="62" r="280" fill="var(--ink-dark)"/>
      <circle cx="520" cy="52" r="264" fill="var(--paper)"/>
    </svg>

    <div class="wordmark">
      <span class="wordmark__square"></span>
      <span class="wordmark__name">Orvane<br>Inspections</span>
    </div>

    <div class="contact">
      <p class="contact__name">Dana Whitfield</p>
      <p class="contact__title">FOUNDER</p>
      <ul class="contact__list">
        <li class="contact__item">
          <svg class="contact__icon" viewBox="0 0 24 24"><path d="M6.6 10.8a15 15 0 0 0 6.6 6.6l2.2-2.2a1 1 0 0 1 1-.25 11.4 11.4 0 0 0 3.6.57 1 1 0 0 1 1 1V20a1 1 0 0 1-1 1A17 17 0 0 1 3 4a1 1 0 0 1 1-1h3.5a1 1 0 0 1 1 1c0 1.25.2 2.45.57 3.57a1 1 0 0 1-.25 1z"/></svg>
          <span>000 000 0000</span>
        </li>
        <li class="contact__item">
          <svg class="contact__icon" viewBox="0 0 24 24"><path d="M2 5h20v14H2z M2 5l10 8 10-8" stroke="var(--card-dark)" stroke-width="1.5"/></svg>
          <span>info@yourmail.com</span>
        </li>
      </ul>
    </div>
  </section>

</body>
</html>
```